One of a kind service business!

We are the only ocean freight auditing company in the entire world that does what we do. We provide a innovative service in auditing our clients invoices for billing errors as it relates to the import and export of their products anywhere in the world. We'd like to retain the current logo - but we are open to any interesting concepts that can complete the card.

Target Market(s)

C-Level and Senior Financial executives

Industry/Entity Type

Auditing

Requirements
Must have

• ONE SIDED ONLY
Should not have
• no cartoonish images

```html
<!DOCTYPE html>
<html lang="en">
<head>
<meta charset="utf-8">
<title>Tidemark Audit – Business Card</title>
<link href="https://fonts.googleapis.com/css2?family=Arimo:wght@400;700&display=swap" rel="stylesheet">
<style>
  :root {
    --backdrop: #d6d8db;
    --card: #ffffff;
    --navy: #17305f;
    --ocean: #2c7eb9;
    --ink: #1d2b4a;
    --icon: #2c7eb9;
    --on-blue: #ffffff;
  }
  * { margin: 0; padding: 0; box-sizing: border-box; }
  html, body {
    width: 1200px;
    height: 944px;
    overflow: hidden;
    background: var(--backdrop);
    font-family: "Arimo", Arial, sans-serif;
  }
  .canvas {
    position: relative;
    width: 1200px;
    height: 944px;
  }
  .card {
    position: absolute;
    left: 100px;
    top: 187px;
    width: 1000px;
    height: 570px;
    background: var(--card);
    border-radius: 34px;
    overflow: hidden;
    box-shadow: 0 10px 24px rgba(0, 0, 0, 0.25);
  }
  .wave {
    position: absolute;
    inset: 0;
    width: 1000px;
    height: 570px;
  }
  .wave .wave-dark { fill: var(--navy); }
  .wave .wave-light { fill: var(--ocean); }

  .brand {
    position: absolute;
    left: 50px;
    top: 86px;
    display: flex;
    align-items: center;
    gap: 16px;
  }
  .brand-mark {
    width: 26px;
    height: 26px;
    background: var(--navy);
  }
  .brand-name {
    font-size: 60px;
    font-weight: 700;
    color: var(--ocean);
    letter-spacing: 1px;
    line-height: 1;
  }

  .contact {
    position: absolute;
    left: 70px;
    top: 212px;
    list-style: none;
    color: var(--ink);
    font-size: 27px;
    line-height: 34px;
  }
  .contact li {
    display: flex;
    align-items: flex-start;
  }
  .contact .icon {
    width: 24px;
    height: 24px;
    margin-top: 5px;
    margin-right: 18px;
    flex: none;
    fill: var(--icon);
  }
  .contact .address-lines { display: block; }
  .contact .gap { margin-top: 20px; }

  .person {
    position: absolute;
    left: 690px;
    top: 448px;
    width: 260px;
    text-align: center;
    color: var(--on-blue);
  }
  .person-name {
    font-size: 39px;
    font-weight: 400;
    line-height: 46px;
  }
  .person-title {
    font-size: 25px;
    line-height: 30px;
  }
</style>
</head>
<body>
<main class="canvas">
  <article class="card">
    <svg class="wave" viewBox="0 0 1000 570" aria-hidden="true">
      <path class="wave-dark" d="M617 0 C720 150 560 330 490 570 L1000 570 L1000 0 Z"/>
      <path class="wave-light" d="M662 0 C770 170 640 360 590 570 L1000 570 L1000 0 Z"/>
    </svg>

    <header class="brand">
      <span class="brand-name">Tidemark Audit</span>
      <span class="brand-mark"></span>
    </header>

    <ul class="contact">
      <li>
        <svg class="icon" viewBox="0 0 24 24"><path d="M12 2 1 12h3v10h6v-6h4v6h6V12h3z"/></svg>
        <span class="address-lines">Harbor Point Offices<br>Vltavska 12, Prague<br>Czech Republic 11000</span>
      </li>
      <li class="gap">
        <svg class="icon" viewBox="0 0 24 24"><path d="M6.6 10.8a15 15 0 0 0 6.6 6.6l2.2-2.2a1 1 0 0 1 1-.25 11.4 11.4 0 0 0 3.6.57 1 1 0 0 1 1 1V20a1 1 0 0 1-1 1A17 17 0 0 1 3 4a1 1 0 0 1 1-1h3.5a1 1 0 0 1 1 1c0 1.25.2 2.45.57 3.57a1 1 0 0 1-.25 1z"/></svg>
        <span>+420 200 555 014</span>
      </li>
      <li>
        <svg class="icon" viewBox="0 0 24 24"><path d="M8 1h8a2 2 0 0 1 2 2v18a2 2 0 0 1-2 2H8a2 2 0 0 1-2-2V3a2 2 0 0 1 2-2zm0 3v14h8V4zm4 15.5a1.2 1.2 0 1 0 0 2.4 1.2 1.2 0 0 0 0-2.4z"/></svg>
        <span>+420 600 555 237</span>
      </li>
      <li>
        <svg class="icon" viewBox="0 0 24 24"><path d="M6.6 10.8a15 15 0 0 0 6.6 6.6l2.2-2.2a1 1 0 0 1 1-.25 11.4 11.4 0 0 0 3.6.57 1 1 0 0 1 1 1V20a1 1 0 0 1-1 1A17 17 0 0 1 3 4a1 1 0 0 1 1-1h3.5a1 1 0 0 1 1 1c0 1.25.2 2.45.57 3.57a1 1 0 0 1-.25 1z"/></svg>
        <span>+1 555 014 2290 - USA</span>
      </li>
      <li>
        <svg class="icon" viewBox="0 0 24 24"><path d="M6 2h10v6H6zM3 9h18a1 1 0 0 1 1 1v8a1 1 0 0 1-1 1h-3v3H6v-3H3a1 1 0 0 1-1-1v-8a1 1 0 0 1 1-1zm5 7v4h8v-4z"/></svg>
        <span>+420 200 555 090</span>
      </li>
      <li>
        <svg class="icon" viewBox="0 0 24 24"><path d="M12 1a11 11 0 1 0 0 22 11 11 0 0 0 0-22zm7.9 10h-3.4a17 17 0 0 0-1.5-6.6A9 9 0 0 1 19.9 11zM12 3.1c1 1.4 2.3 4 2.5 7.9h-5C9.7 7.1 11 4.5 12 3.1zM9 4.4A17 17 0 0 0 7.5 11H4.1A9 9 0 0 1 9 4.4zM4.1 13h3.4A17 17 0 0 0 9 19.6 9 9 0 0 1 4.1 13zm7.9 7.9c-1-1.4-2.3-4-2.5-7.9h5c-.2 3.9-1.5 6.5-2.5 7.9zm3-1.3a17 17 0 0 0 1.5-6.6h3.4a9 9 0 0 1-4.9 6.6z"/></svg>
        <span>www.tidemarkaudit.net</span>
      </li>
      <li>
        <svg class="icon" viewBox="0 0 24 24"><path d="M2 5h20v14H2zm2 2v.5l8 5.5 8-5.5V7zm0 2.9V17h16V9.9l-8 5.5z"/></svg>
        <span>danielm@tidemarkaudit.net</span>
      </li>
    </ul>

    <section class="person">
      <p class="person-name">Daniel Marsh</p>
      <p class="person-title">CEO</p>
    </section>
  </article>
</main>
</body>
</html>
```